Business Card Design Project - 2 sided

We need a business card design for a card having one business on each side (ie. two businesses on one card). Would like a design that incorporates logo, tagline and normal fields (name, position, address, phone).

Would also like an allowance for small font text along the bottom (text to be determined, but less than 50 characters).

NB. Attached logo for Harbor Quill has two variations - either can be used.

www.harborquill-example.com / www.velmaro-example.com

```html
<!DOCTYPE html>
<html lang="en">
<head>
<meta charset="utf-8">
<title>Harbor Quill / Velmaro – Two-sided Business Card</title>
<link rel="stylesheet" href="https://fonts.googleapis.com/css2?family=Source+Sans+3:wght@400;600;700&display=swap">
<style>
  :root {
    --bg: #e9e6e2;
    --card: #ffffff;
    --ink: #3a3a3a;
    --navy: #2e2d6e;
    --name-navy: #2f2f7a;
    --green: #8cc63f;
    --green-dark: #6c9e35;
    --blue: #3b8dc8;
    --rule: #9a9a9a;
    --shadow: rgba(0, 0, 0, 0.28);
  }
  * { box-sizing: border-box; margin: 0; padding: 0; }
  html, body { width: 1200px; height: 412px; overflow: hidden; }
  body {
    background: var(--bg);
    font-family: "Source Sans 3", "Helvetica Neue", Arial, sans-serif;
    color: var(--ink);
    position: relative;
  }
  .card {
    position: absolute;
    top: 64px;
    width: 498px;
    height: 284px;
    background: var(--card);
    box-shadow: 0 4px 10px var(--shadow);
    overflow: hidden;
  }
  .card--harbor { left: 74px; }
  .card--velmaro { left: 629px; }

  .brand {
    position: absolute;
    left: 0;
    width: 278px;
    text-align: center;
  }
  .brand__mark {
    display: inline-flex;
    align-items: center;
    gap: 10px;
  }
  .brand__dot {
    width: 26px; height: 26px; border-radius: 50%;
  }
  .brand__name {
    font-weight: 600;
    letter-spacing: 0.04em;
  }
  .card--harbor .brand { top: 138px; }
  .card--harbor .brand__dot { background: var(--green); }
  .card--harbor .brand__name { font-size: 23px; color: var(--navy); text-transform: uppercase; }
  .card--velmaro .brand { top: 130px; }
  .card--velmaro .brand__dot { background: var(--blue); width: 30px; height: 30px; }
  .card--velmaro .brand__name { font-size: 34px; color: var(--blue); font-weight: 700; letter-spacing: 0; }
  .brand__tagline {
    margin-top: 4px;
    font-size: 10.5px;
    color: #222;
  }
  .card--velmaro .brand__tagline {
    margin-top: 0;
    font-size: 14px;
    font-weight: 700;
    color: #3d3d3d;
  }

  .divider {
    position: absolute;
    left: 278px;
    top: 57px;
    width: 1px;
    height: 147px;
    background: var(--rule);
  }

  .details {
    position: absolute;
    left: 305px;
    top: 62px;
    font-size: 12.5px;
    line-height: 17px;
  }
  .details__name {
    font-size: 17px;
    font-weight: 700;
    color: var(--name-navy);
    margin-bottom: 11px;
  }
  .details__title {
    font-size: 13px;
    font-weight: 400;
  }
  .contact { list-style: none; }
  .contact li { display: flex; align-items: center; gap: 4px; }
  .contact svg { width: 10px; height: 10px; fill: #444; flex: none; }
  .address { margin-top: 10px; }

  .footnote {
    position: absolute;
    left: 0; right: 0;
    top: 230px;
    text-align: center;
    font-size: 9.5px;
    letter-spacing: 0.02em;
    color: #222;
  }

  .band {
    position: absolute;
    left: 0; bottom: 0;
    width: 498px; height: 23px;
  }
  .band__url {
    position: absolute;
    right: 12px;
    bottom: 4px;
    font-size: 12px;
    letter-spacing: 0.32em;
    color: #fff;
  }
</style>
</head>
<body>

<svg width="0" height="0" style="position:absolute" aria-hidden="true">
  <defs>
    <symbol id="icon-phone" viewBox="0 0 10 10"><path d="M2.2 0.6l1.4 1.8-0.8 1c0.6 1.3 1.5 2.2 2.8 2.8l1-0.8 1.8 1.4-0.9 1.6C4.7 8.2 1.8 5.3 0.6 1.5z"/></symbol>
    <symbol id="icon-mobile" viewBox="0 0 10 10"><path d="M2.5 0h5v10h-5zM3.3 1v6.5h3.4V1zM4.4 8.2h1.2v0.9H4.4z"/></symbol>
    <symbol id="icon-fax" viewBox="0 0 10 10"><path d="M2 0.5h6v2.5H2zM0.5 3.5h9v4h-9zM2 6.5h6v3H2z"/></symbol>
    <symbol id="icon-mail" viewBox="0 0 10 10"><path d="M0.5 2h9v6.5h-9zM1.2 2.6L5 5.6l3.8-3z"/></symbol>
    <linearGradient id="green-fade" x1="0" x2="1" y1="0" y2="0">
      <stop offset="0" stop-color="#a4d14f"/>
      <stop offset="1" stop-color="#6c9e35"/>
    </linearGradient>
  </defs>
</svg>

<article class="card card--harbor">
  <div class="brand">
    <div class="brand__mark"><span class="brand__dot"></span><span class="brand__name">Harbor Quill</span></div>
    <p class="brand__tagline">Website Translation and Localisation Specialist...</p>
  </div>
  <div class="divider"></div>
  <div class="details">
    <p class="details__name">Your Name <span class="details__title">/ Title</span></p>
    <ul class="contact">
      <li><svg><use href="#icon-phone"/></svg>123-456-7890</li>
      <li><svg><use href="#icon-mobile"/></svg>123-456-7890</li>
      <li><svg><use href="#icon-fax"/></svg>123-456-7890</li>
      <li><svg><use href="#icon-mail"/></svg>name@website.com</li>
    </ul>
    <p class="address">Complex name, Street name<br>City, State, zip code</p>
  </div>
  <p class="footnote">xxxxxxxxxxxxxxxxxxxxxxxxxxxxxxxxxxxxxxxxxxxxxxxxx</p>
  <div class="band">
    <svg width="498" height="23" aria-hidden="true">
      <polygon points="0,0 266,0 244,23 0,23" fill="var(--green)"/>
      <polygon points="276,0 498,0 498,23 254,23" fill="var(--navy)"/>
    </svg>
    <span class="band__url">www.website.com</span>
  </div>
</article>

<article class="card card--velmaro">
  <div class="brand">
    <div class="brand__mark"><span class="brand__dot"></span><span class="brand__name">Velmaro</span></div>
    <p class="brand__tagline">Professional SEO Services</p>
  </div>
  <div class="divider"></div>
  <div class="details">
    <p class="details__name">Your Name <span class="details__title">/ Title</span></p>
    <ul class="contact">
      <li><svg><use href="#icon-phone"/></svg>123-456-7890</li>
      <li><svg><use href="#icon-mobile"/></svg>123-456-7890</li>
      <li><svg><use href="#icon-fax"/></svg>123-456-7890</li>
      <li><svg><use href="#icon-mail"/></svg>name@website.com</li>
    </ul>
    <p class="address">Complex name, Street name<br>City, State, zip code</p>
  </div>
  <p class="footnote">xxxxxxxxxxxxxxxxxxxxxxxxxxxxxxxxxxxxxxxxxxxxxxxxx</p>
  <div class="band">
    <svg width="498" height="23" aria-hidden="true">
      <polygon points="0,0 266,0 244,23 0,23" fill="url(#green-fade)"/>
      <polygon points="276,0 498,0 498,23 254,23" fill="var(--blue)"/>
    </svg>
    <span class="band__url">www.website.com</span>
  </div>
</article>

</body>
</html>
```